Stationery for use with Ninefold Ridge reports

I would like to get a stationery design that my firm -- Ninefold Ridge Advisory -- will use as a format for reports that we send our clients. I am specifically looking for a design for use on a piece of paper or letterhead -- not business cards or envelopes.

We are an Africa based US risk intelligence and strategy firm that works with multinational corporations operating in West Africa. Our initial thinking is that we would like a color scheme consistent with our existing logo -- however we are open to other color schemes.

Also, we would like to see at least two separate versions: one with our company name and logo, the other without name and logo.

We also would like font recommendations for the stationary design.

The final design should communicate discreet professionalism and a modern approach, but it should not overshadow the words and information printed on the stationery.

Target Market(s)

Multinational corporations that currently use our products.

Font styles to use
Serif
Sans Serif

Requirements
Must have
• Sense of discreet professionalism that will not overshadow the content we put onto the stationery format.
• We would like to see designs with and without our company name/logo.
• Please suggest fonts that would work with the stationery.
Nice to have
• Ideally colors consistent with out existing logo, though we are open to and even encourage other ideas.
Should not have
• No need for business cards or envelopes.

```html
<!DOCTYPE html>
<html lang="en">
<head>
<meta charset="utf-8">
<title>Ninefold Ridge Advisory — Letterhead</title>
<link rel="stylesheet" href="https://fonts.googleapis.com/css2?family=Open+Sans:wght@400&display=swap">
<style>
  :root {
    --backdrop: #e4e5e6;
    --paper: #ffffff;
    --ink: #5a5a5a;
    --ink-soft: #666666;
    --band-ochre: #e0a64a;
    --band-sky: #a9d4ef;
    --header-cool: #d3dee6;
    --header-warm: #f3e4c2;
    --signature-tone: #f1f1f1;
  }
  * { box-sizing: border-box; margin: 0; padding: 0; }
  html, body {
    width: 1200px;
    height: 960px;
    overflow: hidden;
    background: var(--backdrop);
  }
  .canvas {
    position: relative;
    width: 1200px;
    height: 960px;
  }
  .letterhead {
    position: absolute;
    left: 306px;
    top: 58px;
    width: 582px;
    height: 830px;
    background: var(--paper);
    font-family: "Open Sans", "Segoe UI", sans-serif;
    color: var(--ink);
    overflow: hidden;
  }
  .header-image {
    position: absolute;
    left: 0;
    top: 0;
    width: 582px;
    height: 114px;
    background:
      linear-gradient(180deg, rgba(255,255,255,0) 55%, var(--paper) 100%),
      linear-gradient(90deg, var(--header-cool) 0%, var(--header-cool) 55%, var(--header-warm) 100%);
  }
  .date-line {
    position: absolute;
    left: 58px;
    top: 247px;
    font-size: 10px;
    line-height: 16px;
  }
  .letter-body {
    position: absolute;
    left: 58px;
    top: 294px;
    width: 470px;
    font-size: 10px;
    line-height: 21.3px;
    letter-spacing: -0.05px;
  }
  .letter-body p { white-space: nowrap; }
  .letter-body .para-2 { margin-top: 2.4px; }
  .letter-body .para-3 { margin-top: 4.3px; }
  .letter-body .para-4 { margin-top: 7.2px; }
  .letter-body span { display: block; }
  .signature-area {
    position: absolute;
    left: 406px;
    top: 578px;
    width: 118px;
    height: 36px;
    background: var(--signature-tone);
  }
  .signatory {
    position: absolute;
    left: 408px;
    top: 614px;
    font-size: 10px;
    line-height: 12px;
    color: var(--ink-soft);
  }
  .footer-band {
    position: absolute;
    left: 0;
    bottom: 0;
    width: 582px;
    height: 16px;
  }
</style>
</head>
<body>
<div class="canvas">
  <article class="letterhead">
    <div class="header-image" role="img" aria-label="Faded aerial photograph of a coastal city and mountain, blending into the page"></div>

    <p class="date-line">Date, 10 September, 2020</p>

    <section class="letter-body">
      <p class="para-1">
        <span>This is a sample letter that has been placed to demonstrate typing remat (Your Company). letterhead</span>
        <span>design. When positioned properly, it will serve to work in harmony with all other elements letterhead.</span>
        <span>This letterhead design is meant to project an image</span>
      </p>
      <p class="para-2">
        <span>This letterhead design is meant project an image of professionalism reliability. By using simple aligen</span>
        <span>we have created a very spacious feeling. The simplicity suggest&nbsp; rengththe spaciousnes contributes h</span>
        <span>aesthetics the layout. These basic qualities along with the (Your Company)</span>
      </p>
      <p class="para-3">
        <span>look and helps reinforce the (Your Company) brand. letterhead design is meant to project an image p</span>
        <span>design. When positioned properly, it will serve to work in harmony all the other elements letterhead.</span>
        <span>sionalism and reliability.</span>
      </p>
      <p class="para-4">
        <span>This letterhead design is based on the (Form of your logo) form (Your Company) logo. Each stationery</span>
        <span>we have created a very spacious feeling. The simplicity suggests strength the spaciousnes contribute</span>
        <span>part of the (Form of your logo).</span>
      </p>
    </section>

    <div class="signature-area" role="img" aria-label="Handwritten signature of Marcus Adeyemi"></div>
    <p class="signatory">Marcus Adeyemi<br>Manager</p>

    <svg class="footer-band" viewBox="0 0 582 16" aria-hidden="true">
      <polygon points="0,0 476,0 469,16 0,16" fill="var(--band-ochre)"/>
      <polygon points="484,0 582,0 582,16 476,16" fill="var(--band-sky)"/>
    </svg>
  </article>
</div>
</body>
</html>
```